Development of the overall look and feel for the website. www.ReelPalsHub.com

This site is geared as a competitor to some of the major Fan websites. Where we want to be different is making a site geared more towards interaction with the Fans in the Social Media platform.
-Live streaming
-Instant Messaging
-Ability to request and purchase custom digital pieces
-Ability for Models/creators to sell blogs, podcasts, clips, screensavers, etc. through a dedicated online digital store.
-We will also have story like features similar to those found on Photoburst to allow interaction.
-Content Creators keep 85% of earnings

This should be sexy, seductive, bold, and geared towards all spectrums. From Swingers, Kink, Fetish, Milf, College, etc.

Overall the feeling should be Fun with a sense of excitement that is taboo and erotic while not scaring people away.

Trying to find the perfect blend between finding harmony/Norma Whitcombe/GBT/SoloPatron/Velvet Soiree and KRV. Monetization will be most similar to SoloPatron.

Target Market(s)

Target market should be 18+ / All Genders/ All sexuality. I want to be sure to target markets that were traditionally left out from some of the bigger platforms with all lifestyle and gender inclusion.

Industry/Entity Type

Adult Modeling, Adult Website, Streaming, Porn/fetish

Colors

Designer to choose colors to be used in the design.

Requirements
Must have
• Sex Appeal, Curiosity, Call to action, Storyboard to tell what we are about
Nice to have
• uploaded some designs that have overall look/feel.
Should not have
• Sexy but no nudity

```html
<!DOCTYPE html>
<html lang="en">
<head>
<meta charset="utf-8">
<title>Live Video Streaming – ReelPalsHub</title>
<link href="https://fonts.googleapis.com/css2?family=Poppins:wght@400;500;600&display=swap" rel="stylesheet">
<style>
:root{
  --ink:#1e1e1e;
  --muted:#555;
  --icon:#6b6b6b;
  --sidebar:#ebebeb;
  --panel:#ececec;
  --white:#ffffff;
  --green:#2e4a36;
  --green-soft:#d3e4d7;
  --tab-grey:#9d9d9d;
  --border:#c9c9c9;
  --live:#e11d1d;
  --accent:#f2c200;
  --brand:#b0154d;
}
*{box-sizing:border-box;margin:0;padding:0}
html,body{width:1200px;height:712px;overflow:hidden;background:var(--white);font-family:"Poppins",sans-serif;color:var(--ink)}
.app{position:relative;width:1200px;height:712px}
.sidebar{position:absolute;left:0;top:0;width:104px;height:712px;background:var(--sidebar)}
.brand{position:absolute;left:17px;top:24px;width:72px;height:72px;border-radius:50%;border:2px solid var(--brand);display:flex;align-items:center;justify-content:center;font-size:9px;font-weight:600;color:var(--brand)}
.nav-item{position:absolute;left:26px;width:44px;height:32px;display:flex;align-items:center;justify-content:center}
.nav-item svg{width:15px;height:15px;fill:var(--icon)}
.nav-item.active{background:var(--white);border-radius:3px}
.nav-item.active svg{fill:var(--green)}
.nav-item .dot{position:absolute;right:13px;top:6px;width:6px;height:6px;border-radius:50%;background:var(--live)}
.active-bar{position:absolute;left:99px;top:186px;width:4px;height:32px;background:var(--green);border-radius:2px}
.page-title{position:absolute;left:143px;top:28px;font-size:24px;font-weight:400;letter-spacing:.3px}
.box{position:absolute;border:1px solid var(--border);background:var(--white);display:flex;align-items:center;justify-content:center}
.live{left:145px;top:81px;width:104px;height:32px;font-size:12px;gap:5px}
.live i{width:9px;height:9px;border-radius:50%;background:var(--live)}
.live b{font-weight:600}
.volume{left:256px;top:81px;width:135px;height:32px;gap:8px}
.volume .track{width:94px;height:3px;background:#ddd;position:relative}
.volume .track span{position:absolute;left:0;top:0;height:3px;width:52px;background:var(--ink)}
.icon-btn{top:81px;width:38px;height:32px}
.icon-btn svg{width:16px;height:16px;fill:var(--icon)}
.username{position:absolute;left:666px;top:87px;font-size:14px;font-weight:500}
.pro{position:absolute;left:747px;top:86px;width:46px;height:22px;background:var(--green);color:var(--white);font-size:11px;font-weight:600;display:flex;align-items:center;justify-content:center}
.stream{position:absolute;left:145px;top:126px;width:648px;height:424px;border-radius:12px;background:linear-gradient(110deg,#b9b6ae 0%,#cfc6b6 30%,#b88562 50%,#d2b59a 72%,#e9e0cf 100%)}
.store{position:absolute;top:584px;left:0;width:820px}
.store-item{position:absolute;width:90px;margin-left:-45px;text-align:center;font-size:13px;color:#444}
.store-item .circle{width:42px;height:42px;border-radius:50%;background:#e4e4e4;margin:0 auto 10px;display:flex;align-items:center;justify-content:center}
.store-item svg{width:16px;height:16px;fill:#9a9a9a}
.chat-panel{position:absolute;left:821px;top:21px;width:336px;height:630px;background:var(--panel);border-radius:14px}
.tab{position:absolute;top:18px;width:148px;height:41px;display:flex;align-items:center;justify-content:center;font-size:12px;font-weight:500}
.tab.chat{left:13px;background:var(--tab-grey);color:var(--white)}
.tab.attendee{left:174px;background:var(--white);color:var(--green)}
.poll{position:absolute;left:14px;top:74px;width:308px;height:219px;background:var(--green);border-radius:14px;color:var(--white);padding:18px 18px 0}
.poll h3{font-size:16px;font-weight:500;line-height:23px;letter-spacing:.2px}
.poll-row{position:absolute;left:16px;width:276px}
.poll-row .bar{height:5px;background:var(--white);border-radius:3px;position:relative}
.poll-row .bar span{position:absolute;left:0;top:0;height:5px;background:#142419;border-radius:3px 0 0 3px}
.poll-row p{font-size:12px;margin-top:7px}
.msg{position:absolute;font-size:12px;height:30px;display:flex;align-items:center;padding:0 12px;white-space:nowrap}
.msg.in{left:64px;width:177px;background:var(--white)}
.msg.out{left:100px;width:177px;background:var(--green-soft);justify-content:center}
.avatar{position:absolute;width:36px;height:36px;border-radius:50%}
.avatar.him{left:14px;background:radial-gradient(circle at 50% 40%,#c49a7c 0 30%,#1b2b3c 32%)}
.avatar.her{left:287px;background:radial-gradient(circle at 50% 42%,#d7b096 0 28%,#4a342a 30% 50%,#f2f2f2 52%)}
.composer{position:absolute;left:8px;top:579px;width:317px;height:38px;background:var(--white);display:flex;align-items:center;padding-left:12px;font-size:11px;color:#444}
.send{position:absolute;right:8px;top:6px;width:26px;height:26px;border-radius:50%;background:var(--accent);display:flex;align-items:center;justify-content:center}
.send svg{width:13px;height:13px;fill:var(--white)}
</style>
</head>
<body>
<div class="app">
  <aside class="sidebar">
    <div class="brand">ReelPalsHub</div>
    <div class="nav-item" style="top:130px"><svg viewBox="0 0 16 16"><path d="M8 2a7 7 0 0 0-7 7c0 2 .8 3.6 2 4.8h10A7 7 0 0 0 8 2zm0 8.5a1.5 1.5 0 0 1-.6-2.9L10 4.5l-1 3.3A1.5 1.5 0 0 1 8 10.5z"/></svg></div>
    <div class="nav-item active" style="top:186px"><svg viewBox="0 0 16 16"><rect x="1" y="4" width="10" height="8" rx="1"/><path d="M11 7l4-2.5v7L11 9z"/></svg><span class="dot"></span></div>
    <div class="active-bar"></div>
    <div class="nav-item" style="top:245px"><svg viewBox="0 0 16 16"><path d="M8 1.5a4.5 4.5 0 0 0-4.5 4.5v3.5L2 12h12l-1.5-2.5V6A4.5 4.5 0 0 0 8 1.5zM6.5 13a1.5 1.5 0 0 0 3 0z"/></svg></div>
    <div class="nav-item" style="top:302px"><svg viewBox="0 0 16 16"><path d="M8 2C4.1 2 1 4.4 1 7.3c0 1.4.7 2.6 1.9 3.6L2 14l3.5-1.8c.8.2 1.6.4 2.5.4 3.9 0 7-2.4 7-5.3S11.9 2 8 2z"/></svg></div>
    <div class="nav-item" style="top:360px"><svg viewBox="0 0 16 16"><circle cx="8" cy="5" r="2.5"/><circle cx="3.5" cy="6.5" r="1.8"/><circle cx="12.5" cy="6.5" r="1.8"/><path d="M3.5 13a4.5 4.5 0 0 1 9 0zM0 13a3.5 3.5 0 0 1 3.5-3.5v3.5zM16 13a3.5 3.5 0 0 0-3.5-3.5v3.5z"/></svg></div>
    <div class="nav-item" style="top:418px"><svg viewBox="0 0 16 16"><path d="M1 2h1v11h13v1H1z"/><rect x="4" y="7" width="1.5" height="5"/><rect x="7" y="5" width="1.5" height="7"/><rect x="10" y="8" width="1.5" height="4"/><rect x="13" y="6" width="1.5" height="6"/></svg></div>
  </aside>

  <h1 class="page-title">Live Video Streaming</h1>
  <div class="box live"><i></i><b>LIVE</b> 23:15:20</div>
  <div class="box volume"><svg width="14" height="12" viewBox="0 0 16 14"><path d="M1 4.5h3L8 1v12L4 9.5H1z" fill="#333"/><path d="M10.5 4a4 4 0 0 1 0 6M12.5 2a7 7 0 0 1 0 10" stroke="#333" stroke-width="1.4" fill="none"/></svg><div class="track"><span></span></div></div>
  <div class="box icon-btn" style="left:526px"><svg viewBox="0 0 16 16"><circle cx="3" cy="8" r="1.7"/><circle cx="8" cy="8" r="1.7"/><circle cx="13" cy="8" r="1.7"/></svg></div>
  <div class="box icon-btn" style="left:572px"><svg viewBox="0 0 16 16"><path d="M7 1h2l.4 2 1.4.6 1.7-1.1 1.4 1.4-1.1 1.7.6 1.4 2 .4v2l-2 .4-.6 1.4 1.1 1.7-1.4 1.4-1.7-1.1-1.4.6L9 15H7l-.4-2-1.4-.6-1.7 1.1-1.4-1.4 1.1-1.7L2.6 9 1 9V7l2-.4.6-1.4-1.1-1.7 1.4-1.4 1.7 1.1L6.6 3zM8 5.5a2.5 2.5 0 1 0 0 5 2.5 2.5 0 0 0 0-5z"/></svg></div>
  <div class="box icon-btn" style="left:618px"><svg viewBox="0 0 16 16"><circle cx="8" cy="5" r="3.5"/><path d="M1 15c0-3.5 3-5.5 7-5.5s7 2 7 5.5z"/></svg></div>
  <div class="username">Username</div>
  <div class="pro">PRO</div>

  <div class="stream" role="img" aria-label="Live stream video feed of the creator smiling at the camera in a bright kitchen"></div>

  <div class="store">
    <div class="store-item" style="left:308px"><div class="circle"><svg viewBox="0 0 16 16"><circle cx="4" cy="12" r="2"/><path d="M2 6a8 8 0 0 1 8 8H8a6 6 0 0 0-6-6zM2 1a13 13 0 0 1 13 13h-2A11 11 0 0 0 2 3z"/></svg></div>Blogs</div>
    <div class="store-item" style="left:386px"><div class="circle"><svg viewBox="0 0 16 16"><rect x="5.5" y="1" width="5" height="9" rx="2.5"/><path d="M3 7.5h1.3a3.7 3.7 0 0 0 7.4 0H13a5 5 0 0 1-4.3 4.9V15H7.3v-2.6A5 5 0 0 1 3 7.5z"/></svg></div>Podcasts</div>
    <div class="store-item" style="left:464px"><div class="circle"><svg viewBox="0 0 16 16"><path d="M3 3h10v7H3zm1 1v5h8V4zM1 11h14v1.5H1z"/></svg></div>Clips</div>
    <div class="store-item" style="left:556px"><div class="circle"><svg viewBox="0 0 16 16"><path d="M4.5 1h7v14h-7zm1 1.5v10h5v-10zM7 13.2h2v.8H7z"/></svg></div>Screensavers</div>
    <div class="store-item" style="left:649px"><div class="circle"><svg viewBox="0 0 16 16"><circle cx="3" cy="8" r="1.7"/><circle cx="8" cy="8" r="1.7"/><circle cx="13" cy="8" r="1.7"/></svg></div>More</div>
  </div>

  <section class="chat-panel">
    <div class="tab chat">Chat (4)</div>
    <div class="tab attendee">Attendee</div>
    <div class="poll">
      <h3>Excepteur sint occaecat on pr oident, sunt in culpa</h3>
      <div class="poll-row" style="top:100px"><div class="bar"><span style="width:124px"></span></div><p>33% Linkbook</p></div>
      <div class="poll-row" style="top:144px"><div class="bar"><span style="width:161px"></span></div><p>60% Linkbook</p></div>
      <div class="poll-row" style="top:187px"><div class="bar"><span style="width:69px"></span></div><p>23% Chirpline</p></div>
    </div>

    <div class="avatar him" style="top:319px" role="img" aria-label="Profile photo of a male fan"></div>
    <div class="msg in" style="top:321px">Nemo enim ipsam volupta</div>
    <div class="msg out" style="top:361px">Nemo enim ipsam volupta</div>
    <div class="avatar her" style="top:358px" role="img" aria-label="Profile photo of the creator"></div>

    <div class="avatar him" style="top:403px" role="img" aria-label="Profile photo of a male fan"></div>
    <div class="msg in" style="top:405px">Nemo enim ipsam volupta</div>
    <div class="msg out" style="top:449px">Nemo enim ipsam volupta</div>
    <div class="avatar her" style="top:446px" role="img" aria-label="Profile photo of the creator"></div>

    <div class="avatar him" style="top:490px" role="img" aria-label="Profile photo of a male fan"></div>
    <div class="msg in" style="top:492px">Nemo enim ipsam volupta</div>
    <div class="msg out" style="top:532px">Nemo enim ipsam volupta</div>
    <div class="avatar her" style="top:529px" role="img" aria-label="Profile photo of the creator"></div>

    <div class="composer">Type message here
      <div class="send"><svg viewBox="0 0 16 16"><path d="M15 1L1 7l5 2 2 5z"/></svg></div>
    </div>
  </section>
</div>
</body>
</html>
```